Cat-products company needs smart, yet endearing, business card

We need a business card design for a new, but up-and-running, business based in Honolulu, Hawaii. The business is Purrnest Nook Co. Our first product is the most environmentally-friendly cat grass kit ever seen on the planet. Future products, currently in the R&D phase, will include a variety of exciting cat scratchers. We also do consulting work to help apartment-dwellers make their home more cat-friendly and, in the future, plan on doing full, custom installs of structure to create high walkways for cats.

Target Market(s)

Middle-aged, apartment-dwelling, middle-class workers who own 1 or more cats and who dote on them.

Industry/Entity Type

Pet Care

Contact Information for Business Card

A striking, professional, yet warm and friendly design is what we're after.

Font styles to use
Serif
Sans Serif
Other font styles liked:
• Comfortaa

Colors

Designer to choose colors to be used in the design.

Requirements
Must have
• The company logo: (see attachment)
• The company name: Purrnest Nook Co
• The web address: www.purrnestnookco.com
• Email: support@purrnestnookco.com
• Phone: +1 (808) 571 6023
• Update (Fri Jun 30 3017 7:45pm Hawaii Time) I would like, is possible, uploaded picture of the cat grass kit on the back of the card with some text along the lines of: Purrnest Nook Co - Maker Of The Leafiest Feline Sprout Set Yet
Nice to have
• A cat picture, cartoon, real or silhouette that illustrates cats in action and/or relaxing; ie using the apartment space to live, play and relax in and being well-contented.
• Most of the website is done in the font: Comfortaa. It might be nice to continue using this for brand consistency.
Should not have
• Hard-to-read fonts.

```html
<!DOCTYPE html>
<html lang="en">
<head>
<meta charset="utf-8">
<title>Purrnest Nook Co — Business Card</title>
<link rel="stylesheet" href="https://fonts.googleapis.com/css2?family=Comfortaa:wght@700&family=Open+Sans:wght@400;500&display=swap">
<style>
  :root {
    --page-bg: #e9e6e2;
    --card-bg: #f7f6f4;
    --brand-brown: #58342f;
    --brand-yellow: #f9b200;
    --ink-dark: #2b2220;
    --ink-light: #ffffff;
  }
  * { margin: 0; padding: 0; box-sizing: border-box; }
  html, body {
    width: 1200px;
    height: 900px;
    overflow: hidden;
    background: var(--page-bg);
  }
  .business-card {
    position: absolute;
    left: 111px;
    top: 148px;
    width: 978px;
    height: 603px;
    background: var(--card-bg);
    box-shadow: 0 10px 30px rgba(0,0,0,0.15);
    overflow: hidden;
    font-family: "Open Sans", Arial, sans-serif;
  }
  .card-shapes {
    position: absolute;
    inset: 0;
    width: 100%;
    height: 100%;
  }
  .brand-lockup {
    position: absolute;
    left: 55px;
    top: 122px;
    display: flex;
    align-items: center;
    gap: 24px;
  }
  .brand-square {
    width: 78px;
    height: 78px;
    background: var(--brand-yellow);
  }
  .brand-name {
    font-family: "Comfortaa", Arial, sans-serif;
    font-weight: 700;
    font-size: 48px;
    color: var(--brand-brown);
    white-space: nowrap;
  }
  .person {
    position: absolute;
    left: 54px;
    top: 470px;
  }
  .person-name {
    font-size: 30px;
    font-weight: 500;
    color: var(--brand-yellow);
    letter-spacing: 0.5px;
    text-transform: uppercase;
    line-height: 1.1;
  }
  .person-title {
    font-size: 20px;
    color: var(--ink-dark);
    margin-top: 4px;
  }
  .contact-list {
    position: absolute;
    right: 36px;
    top: 350px;
    list-style: none;
    text-align: right;
  }
  .contact-item {
    display: flex;
    justify-content: flex-end;
    align-items: center;
    gap: 10px;
    font-size: 21px;
    color: var(--ink-light);
    height: 35px;
  }
  .contact-icon {
    width: 20px;
    height: 20px;
    fill: var(--brand-yellow);
    flex: none;
  }
</style>
</head>
<body>
  <div class="business-card">
    <svg class="card-shapes" viewBox="0 0 652 402" preserveAspectRatio="none" aria-hidden="true">
      <polyline points="370,367 370,300 310,300 536,80 652,188"
                fill="none" stroke="var(--brand-yellow)" stroke-width="9" stroke-linejoin="round" stroke-linecap="round"/>
      <path d="M316 296 L536 86 L652 194 L652 402 L0 402 L0 367 L366 367 L366 296 Z"
            fill="var(--brand-brown)"/>
    </svg>

    <div class="brand-lockup">
      <div class="brand-square"></div>
      <span class="brand-name">Purrnest Nook Co</span>
    </div>

    <div class="person">
      <p class="person-name">Leilani Ortega</p>
      <p class="person-title">Managing Director</p>
    </div>

    <ul class="contact-list">
      <li class="contact-item">
        <span>+1 (808) 571 6023</span>
        <svg class="contact-icon" viewBox="0 0 24 24" aria-hidden="true"><path d="M6.6 10.8a15.1 15.1 0 0 0 6.6 6.6l2.2-2.2c.3-.3.7-.4 1-.2 1.1.4 2.3.6 3.6.6.6 0 1 .4 1 1V20c0 .6-.4 1-1 1C10.6 21 3 13.4 3 4c0-.6.4-1 1-1h3.5c.6 0 1 .4 1 1 0 1.3.2 2.5.6 3.6.1.3 0 .7-.2 1z"/></svg>
      </li>
      <li class="contact-item">
        <span>support@purrnestnookco.com</span>
        <svg class="contact-icon" viewBox="0 0 24 24" aria-hidden="true"><path d="M3 5h18v14H3z M3 6l9 7 9-7" fill="var(--brand-yellow)" stroke="var(--brand-brown)" stroke-width="1.5"/></svg>
      </li>
      <li class="contact-item">
        <span>www.purrnestnookco.com</span>
        <svg class="contact-icon" viewBox="0 0 24 24" aria-hidden="true"><circle cx="12" cy="12" r="9"/><path d="M3 12h18M12 3c3 3 3 15 0 18M12 3c-3 3-3 15 0 18" fill="none" stroke="var(--brand-brown)" stroke-width="1.3"/></svg>
      </li>
    </ul>
  </div>
</body>
</html>
```